Redesign a Start-Up Dating Website

Website: https://morvelique.com.
Make sure the design has an island style theme.
I would like the 7 pages of my website to have a new and professional look. I want the same colors to remain, but I want a creative look for all the pages. This is a dating website that is in the startup stage. So, I want to give my entire website a custom makeover. I want something that will stand out from the other dating sites. Something that will attract more people to want to use my services, and hopefully get new members.
Target Market(s)
Dating
Industry/Entity Type
Dating
Coding
Coded - Design and coding required
Number of Pages Required
5+ page
Font styles to use
Other font styles liked:
- Decorative, San Serif
Requirements
Must have
- The design must have the original colors and a stylish font to go along. The design must be creative, welcoming, and professional. I would like an island style theme for the website. This is a dating website so make sure that the design is tailored to that aspect.
Nice to have
- It would be nice to have a decorative font and a professional style on all the pages. Make sure the design will be mobile responsive and friendly for all the pages on the website.
Should not have
- The design should not be bland and uncreative.

```html
<!DOCTYPE html>
<html lang="en">
<head>
<meta charset="utf-8">
<title>Morvelique – Online Dating</title>
<link href="https://fonts.googleapis.com/css2?family=Open+Sans:wght@400;600;700&display=swap" rel="stylesheet">
<style>
:root{
  --orange:#f7941d;
  --teal:#2fb39c;
  --teal-soft:#5cb7a0;
  --purple:#6b45a8;
  --purple-band:#7a52b8;
  --grey-band:#ececed;
  --ink:#1f1f1f;
  --muted:#444;
  --white:#fff;
  --panel:rgba(40,40,40,.82);
}
*{box-sizing:border-box;margin:0;padding:0}
html,body{width:1200px;height:2426px;overflow:hidden}
body{position:relative;font-family:"Open Sans",Arial,sans-serif;color:var(--ink);background:var(--white)}
.abs{position:absolute}

/* header */
.site-header{left:0;top:0;width:1200px;height:78px;background:var(--white)}
.brand{left:133px;top:16px;display:flex;align-items:center;gap:8px}
.brand-dot{width:40px;height:40px;border-radius:50%;background:var(--orange)}
.brand-name{font-weight:700;font-size:29px;color:var(--teal)}
.main-nav{left:0;top:0;width:1200px;height:78px}
.main-nav a{position:absolute;top:32px;font-size:11px;line-height:16px;color:var(--ink);text-decoration:none;text-transform:uppercase;white-space:nowrap}
.main-nav a.active{background:var(--orange);color:var(--white);padding:0 5px;margin-left:-5px}
.btn-login,.btn-register{top:27px;height:26px;font-size:11px;font-weight:600;display:flex;align-items:center;justify-content:center}
.btn-login{left:937px;width:53px;border:2px solid var(--teal-soft);color:var(--teal-soft)}
.btn-register{left:997px;width:69px;background:var(--teal-soft);color:var(--white)}

/* hero */
.hero{left:0;top:78px;width:1200px;height:536px;background:linear-gradient(90deg,#c9a792 0%,#e8ddd2 30%,#d9d1c8 60%,#b7a8a0 80%,#e9e4de 100%)}
.hero-arrow{top:328px;width:36px;height:36px;background:rgba(40,40,40,.75);display:flex;align-items:center;justify-content:center}
.search-panel{left:437px;top:78px;width:294px;height:536px;background:var(--panel);color:var(--white);padding:24px 24px 0}
.search-panel h2{font-size:15px;font-weight:700}
.search-panel .lead{font-size:12px;margin-top:3px;margin-bottom:16px}
.field{background:var(--white);height:34px;margin-bottom:16px;padding:5px 10px;color:var(--ink);position:relative}
.field small{display:block;font-size:8px;text-transform:uppercase}
.field strong{display:block;font-size:10px;font-weight:700;text-transform:uppercase}
.field svg{position:absolute;right:12px;top:14px}
.search-btn{height:42px;background:var(--orange);color:var(--white);font-weight:700;font-size:16px;display:flex;align-items:center;justify-content:center}
.panel-note{text-align:center;font-size:14px;margin-top:28px;line-height:1.4}
.panel-note b{font-weight:700}

/* members */
.section-title{left:0;width:1200px;text-align:center;font-size:18px;font-weight:400;line-height:1.45}
.section-title .accent{display:block;color:var(--orange);font-weight:700;font-size:19px}
.member{width:179px}
.member .photo{width:179px;height:194px}
.member .name{margin-top:14px;color:var(--purple);font-size:12px;font-weight:600;text-transform:uppercase}
.member .meta{font-size:10px;margin-top:1px}
.member .rule{height:1px;background:#ddd;margin-top:12px}
.member .info{font-size:9px;margin-top:13px;display:flex;align-items:center;gap:6px;text-transform:uppercase}
.carousel-arrow{top:858px}

/* benefits */
.benefits{left:0;top:1100px;width:1200px;height:577px;background:var(--grey-band)}
.benefits h3{position:absolute;top:44px;width:1200px;text-align:center;color:var(--orange);font-size:19px;font-weight:700}
.benefits .sub{position:absolute;top:90px;width:1200px;text-align:center;font-size:15px;line-height:1.35;text-transform:uppercase}
.benefit{width:330px;text-align:center}
.benefit .icon{width:120px;height:120px;border-radius:50%;background:var(--teal);margin:0 auto;display:flex;align-items:center;justify-content:center}
.benefit h4{margin-top:40px;color:var(--purple);font-size:12px;font-weight:700;text-transform:uppercase}
.benefit p{margin-top:18px;font-size:12px;line-height:1.55;color:var(--muted)}
.btn-orange{background:var(--orange);color:var(--white);font-weight:700;display:flex;align-items:center;justify-content:center;text-transform:uppercase}

/* promo band */
.promo{left:0;top:1677px;width:1200px;height:357px;background:var(--purple-band);text-align:center;color:var(--white)}
.promo h3{position:absolute;top:78px;width:1200px;color:var(--orange);font-size:29px;font-weight:700}
.promo p{position:absolute;top:146px;width:1200px;font-size:15px;line-height:1.45;text-transform:uppercase}

/* footer */
.footer{left:0;top:2034px;width:1200px;height:275px;background:var(--teal);color:var(--white)}
.footer h5{font-size:11px;font-weight:700;text-transform:uppercase}
.footer-links{font-size:11px;line-height:1.6;margin-top:20px;list-style:none}
.subscribe-input{width:247px;height:39px;background:#f2f2f2;margin-top:14px;display:flex;align-items:center;padding-left:14px;gap:10px;font-size:10px;color:#666}
.footer .small{font-size:10px;line-height:1.7;margin-top:20px}
.footer .about{font-size:10px;line-height:1.6;margin-top:14px;width:255px;text-align:justify}

.bottom-bar{left:0;top:2309px;width:1200px;height:117px;background:var(--white)}
.follow{left:480px;top:2351px;display:flex;align-items:center;gap:8px;font-size:10px}
.social{width:28px;height:28px;border-radius:50%;background:#2e4e8f}
.copyright{left:833px;top:2356px;font-size:10px}
</style>
</head>
<body>

<header class="site-header abs">
  <div class="brand abs"><span class="brand-dot"></span><span class="brand-name">Morvelique</span></div>
  <nav class="main-nav abs">
    <a class="active" href="#" style="left:464px">Home</a>
    <a href="#" style="left:519px">Search</a>
    <a href="#" style="left:587px">Members</a>
    <a href="#" style="left:668px">Extras</a>
    <a href="#" style="left:731px">About</a>
    <a href="#" style="left:784px">Premium</a>
    <a href="#" style="left:859px">Contact</a>
  </nav>
  <div class="btn-login abs">Login</div>
  <div class="btn-register abs">Register</div>
</header>

<div class="hero abs" role="img" aria-label="Photo of a smiling couple sitting face to face at a cafe table"></div>
<div class="hero-arrow abs" style="left:0"><svg width="10" height="12"><path d="M7 1L2 6l5 5" stroke="#fff" stroke-width="2" fill="none"/></svg></div>
<div class="hero-arrow abs" style="left:1164px"><svg width="10" height="12"><path d="M3 1l5 5-5 5" stroke="#fff" stroke-width="2" fill="none"/></svg></div>

<form class="search-panel abs">
  <h2>QUICK SEARCH</h2>
  <p class="lead">Let's Find Your Perfect Match Today</p>
  <div class="field"><small>I am</small><strong>Man</strong><svg width="10" height="6"><path d="M0 0h10L5 6z" fill="#222"/></svg></div>
  <div class="field"><small>Seeking a</small><strong>Woman</strong><svg width="10" height="6"><path d="M0 0h10L5 6z" fill="#222"/></svg></div>
  <div class="field"><small>Age</small><strong>18</strong><svg width="10" height="6"><path d="M0 0h10L5 6z" fill="#222"/></svg></div>
  <div class="field"><small>To</small><strong>99</strong><svg width="10" height="6"><path d="M0 0h10L5 6z" fill="#222"/></svg></div>
  <div class="field"><small>Country</small><strong>Afghanistan</strong><svg width="10" height="6"><path d="M0 0h10L5 6z" fill="#222"/></svg></div>
  <div class="search-btn">SEARCH</div>
  <p class="panel-note">Find Your<br><b>Perfect Match For Free!</b></p>
  <p class="panel-note" style="margin-top:30px"><b>Online Dating</b><br>Made Easy On Morvelique.Com</p>
</form>

<h2 class="section-title abs" style="top:654px">JOIN THIS COMMUNITY OF<span class="accent">1 MORVELIQUE MEMBERS</span></h2>

<svg class="carousel-arrow abs" style="left:76px" width="14" height="22"><path d="M12 1L2 11l10 10" stroke="#999" stroke-width="2" fill="none"/></svg>
<svg class="carousel-arrow abs" style="left:1106px" width="14" height="22"><path d="M2 1l10 10-10 10" stroke="#999" stroke-width="2" fill="none"/></svg>

<div class="member abs" style="left:133px;top:755px">
  <div class="photo" role="img" aria-label="Member portrait photo" style="background:#d9b9a8"></div>
  <div class="name">Selin</div><div class="meta">Age 16, Germany</div><div class="rule"></div>
  <div class="info">View info <svg width="5" height="7"><path d="M0 0l5 3.5L0 7z" fill="#222"/></svg></div>
</div>
<div class="member abs" style="left:320px;top:755px">
  <div class="photo" role="img" aria-label="Member portrait photo" style="background:#5b4f55"></div>
  <div class="name">Benji</div><div class="meta">Age 28, United States</div><div class="rule"></div>
  <div class="info">View info <svg width="5" height="7"><path d="M0 0l5 3.5L0 7z" fill="#222"/></svg></div>
</div>
<div class="member abs" style="left:509px;top:755px">
  <div class="photo" role="img" aria-label="Member portrait photo" style="background:#e7dccd"></div>
  <div class="name">Mara Jo</div><div class="meta">Age 16, Germany</div><div class="rule"></div>
  <div class="info">View info <svg width="5" height="7"><path d="M0 0l5 3.5L0 7z" fill="#222"/></svg></div>
</div>
<div class="member abs" style="left:698px;top:755px">
  <div class="photo" role="img" aria-label="Member portrait photo" style="background:#b59a82"></div>
  <div class="name">Ricardo</div><div class="meta">Age 16, Canada</div><div class="rule"></div>
  <div class="info">View info <svg width="5" height="7"><path d="M0 0l5 3.5L0 7z" fill="#222"/></svg></div>
</div>
<div class="member abs" style="left:886px;top:755px">
  <div class="photo" role="img" aria-label="Member portrait photo" style="background:#9c9a98"></div>
  <div class="name">Pietro</div><div class="meta">Age 16, Germany</div><div class="rule"></div>
  <div class="info">View info <svg width="5" height="7"><path d="M0 0l5 3.5L0 7z" fill="#222"/></svg></div>
</div>

<section class="benefits abs">
  <h3>BENEFITS</h3>
  <p class="sub">Affordable &nbsp;Easy sign-up<br>and cancellation processes</p>

  <div class="benefit abs" style="left:95px;top:176px">
    <div class="icon"><svg width="56" height="56" viewBox="0 0 56 56"><rect x="6" y="10" width="44" height="38" rx="4" fill="#fff"/><rect x="18" y="5" width="4" height="10" fill="#fff"/><rect x="34" y="5" width="4" height="10" fill="#fff"/><circle cx="20" cy="28" r="5" fill="var(--teal)"/><rect x="13" y="34" width="14" height="7" rx="3" fill="var(--teal)"/><rect x="31" y="25" width="13" height="3" fill="var(--teal)"/><rect x="31" y="32" width="13" height="3" fill="var(--teal)"/></svg></div>
    <h4>Create a profile</h4>
    <p>Let people know all about you; the good<br>and the quirky-show the world your true<br>colors and find someone with the same<br>unique qualities as you.</p>
  </div>
  <div class="benefit abs" style="left:436px;top:176px">
    <div class="icon"><svg width="56" height="56" viewBox="0 0 56 56"><circle cx="24" cy="24" r="16" fill="none" stroke="#fff" stroke-width="6"/><path d="M35 35l13 13" stroke="#fff" stroke-width="7" stroke-linecap="round"/><circle cx="24" cy="20" r="5" fill="#fff"/><path d="M15 32a9 8 0 0 1 18 0z" fill="#fff"/></svg></div>
    <h4>Find matches</h4>
    <p>Browse other users and feel the excitement<br>of getting your first message and getting to<br>know potential dates in a safe and fun<br>environment.</p>
  </div>
  <div class="benefit abs" style="left:783px;top:176px">
    <div class="icon"><svg width="60" height="56" viewBox="0 0 60 56"><path d="M30 16l-5-5a3.5 3.5 0 0 1 5-5 3.5 3.5 0 0 1 5 5z" fill="#fff"/><circle cx="18" cy="28" r="6" fill="#fff"/><circle cx="42" cy="28" r="6" fill="#fff"/><path d="M8 50a10 12 0 0 1 20 0z" fill="#fff"/><path d="M32 50a10 12 0 0 1 20 0z" fill="#fff"/></svg></div>
    <h4>Start dating</h4>
    <p>Once you've found your potential soulmate,<br>it's time to meet up and say 'Hello' to the<br>start of your journey together</p>
  </div>

  <div class="btn-orange abs" style="left:474px;top:483px;width:252px;height:41px;font-size:15px">View membership plans</div>
</section>

<section class="promo abs" role="img" aria-label="Purple band over a faded mosaic of member portraits">
  <h3>DATING IS EASY WITH MORVELIQUE</h3>
  <p>Sign-up for a 30 days free trial enjoy all the benefits<br>Morvelique has to offer with a full membership.</p>
  <div class="btn-orange abs" style="left:412px;top:223px;width:375px;height:42px;font-size:15px">Start Morveliquing with free signup</div>
</section>

<footer class="footer abs">
  <div class="abs" style="left:133px;top:44px">
    <h5>Links</h5>
    <ul class="footer-links"><li>Morvelique</li><li>About</li><li>Contact</li><li>Login</li><li>Members</li><li>Premium</li><li>Register</li><li>Search</li></ul>
  </div>
  <div class="abs" style="left:288px;top:44px">
    <h5>Subscribe for updates</h5>
    <div class="subscribe-input"><svg width="12" height="9"><rect x=".5" y=".5" width="11" height="8" fill="none" stroke="#888"/><path d="M.5 .5l5.5 4 5.5-4" fill="none" stroke="#888"/></svg>E mail id</div>
    <div class="btn-orange" style="width:88px;height:30px;font-size:10px;margin-top:14px">Subscribe</div>
  </div>
  <div class="abs" style="left:606px;top:44px">
    <h5>Contact us</h5>
    <p class="small">Palm Cove, Isla Verde,<br>00840</p>
    <p class="small" style="margin-top:12px">contact@morvelique.com</p>
  </div>
  <div class="abs" style="left:812px;top:44px">
    <h5>About</h5>
    <p class="about">Morvelique aims to provide a straight-forward, easy-to-use online dating service. I won't over-complicate things or reduce the amount of people you can talk to with algorithms. I know that sometimes, opposites attract and sparks can fly with the last person you thought you'd be interested in-so I won't hide anybody from you. There is no discrimination on this dating site, it's not only about accepting young singles. I think everybody deserves</p>
  </div>
</footer>

<div class="bottom-bar abs"></div>
<div class="brand abs" style="top:2340px"><span class="brand-dot"></span><span class="brand-name">Morvelique</span></div>
<div class="follow abs">Follow us : <span class="social"></span><span class="social" style="background:#2b7fc4"></span><span class="social" style="background:#2a5d94"></span></div>
<div class="copyright abs">Copyright © Morvelique 2017 . All rights reserved.</div>

</body>
</html>
```